Anzeigengestaltung für Unternehmensberatung für Pflegedienste
Zielgruppe
Wir sind eine Unternehmensberatung für Pflegedienste. Es soll eine Werbeanzeige erstellt werden, mit welcher schlecht laufende Pflegedienste, die gerade in einer Krise stecken angesprochen werden,
Der slogan soll einfach klingen : Pflege neu gedaxht: wirtschaftlich, nachhaltig, zukunftssicher
Anzeige in 3 Formaten
1. Format 55.3 mm x 118 mm
2. Format 1/ halbe Seite Quer 176 x 118 mm un
3. Format d 1 x A4 _Seite
Der Name der Firma Tolvek GmbH info at tolvek-beispiel.de Tel 0555 91827364 aus Rostock Berlin und bundesweit tätig
Aufgabenstellung
Kreativ und elegant

```html
<!DOCTYPE html>
<html lang="de">
<head>
<meta charset="utf-8">
<title>Tolvek GmbH – Pflege neu gedacht</title>
<link rel="stylesheet" href="https://fonts.googleapis.com/css2?family=Inter:wght@300;400;500;600&display=swap">
<style>
  :root {
    --paper: #f1ece4;
    --navy: #1c3350;
    --ink: #22262b;
    --gold: #b89a66;
    --wave-blue: #3f6d9c;
    --wave-light: #c9d3dd;
    --rule: #d6c7ad;
    --divider: #b9b2a6;
  }
  * { margin: 0; padding: 0; box-sizing: border-box; }
  html, body { width: 1200px; height: 900px; overflow: hidden; background: var(--paper); }
  .ad {
    position: relative;
    width: 1200px; height: 900px;
    background: var(--paper);
    font-family: "Inter", Arial, sans-serif;
    color: var(--ink);
  }
  .brand {
    position: absolute; top: 42px; left: 0; width: 100%;
    text-align: center;
    font-size: 84px; font-weight: 600; letter-spacing: 4px;
    color: var(--navy);
  }
  .wave { position: absolute; left: 0; top: 220px; width: 1200px; height: 300px; }
  .puzzle-visual {
    position: absolute; left: 450px; top: 176px; width: 302px; height: 344px;
    border-radius: 10px;
    background: linear-gradient(135deg, var(--navy) 0%, var(--navy) 48%, var(--gold) 52%, #9d7f52 100%);
  }
  .slogan {
    position: absolute; top: 556px; left: 0; width: 100%;
    text-align: center;
    font-size: 39px; font-weight: 300; line-height: 1.22;
    color: var(--ink);
  }
  .columns {
    position: absolute; top: 708px; left: 44px; width: 1112px;
    display: grid; grid-template-columns: repeat(4, 1fr);
  }
  .column { padding: 0 20px 0 18px; border-left: 1px solid var(--divider); }
  .column:first-child { border-left: none; padding-left: 0; }
  .column-title { font-size: 15px; font-weight: 500; margin-bottom: 22px; }
  .column-text { font-size: 14px; line-height: 1.45; color: #3a3d42; }
  .footer-rule {
    position: absolute; top: 832px; left: 44px; width: 1112px;
    height: 1px; background: var(--rule);
  }
  .footer {
    position: absolute; top: 856px; left: 44px; width: 1112px;
    display: flex; justify-content: space-between;
    font-size: 16px; font-weight: 400; color: var(--navy);
  }
</style>
</head>
<body>
<div class="ad">
  <div class="brand">TOLVEK</div>

  <svg class="wave" viewBox="0 0 1200 300" aria-hidden="true">
    <defs>
      <linearGradient id="waveFill" x1="0" y1="0" x2="1" y2="0">
        <stop offset="0" stop-color="#f1ece4"/>
        <stop offset="0.12" stop-color="#c9d3dd"/>
        <stop offset="0.38" stop-color="#3f6d9c"/>
        <stop offset="0.62" stop-color="#3f6d9c"/>
        <stop offset="0.88" stop-color="#c9d3dd"/>
        <stop offset="1" stop-color="#f1ece4"/>
      </linearGradient>
      <linearGradient id="waveFade" x1="0" y1="0" x2="0" y2="1">
        <stop offset="0" stop-color="#f1ece4" stop-opacity="0"/>
        <stop offset="1" stop-color="#f1ece4" stop-opacity="0.25"/>
      </linearGradient>
    </defs>
    <path d="M0 40 C 120 10, 220 40, 340 120 C 460 200, 520 190, 600 190 C 680 190, 740 200, 860 120 C 980 40, 1080 10, 1200 40 L 1200 300 L 0 300 Z" fill="url(#waveFill)"/>
    <path d="M0 40 C 120 10, 220 40, 340 120 C 460 200, 520 190, 600 190 C 680 190, 740 200, 860 120 C 980 40, 1080 10, 1200 40 L 1200 300 L 0 300 Z" fill="url(#waveFade)"/>
  </svg>

  <div class="puzzle-visual" role="img" aria-label="Vier ineinandergreifende Puzzleteile in Dunkelblau und Gold als Sinnbild für passende Lösungen"></div>

  <p class="slogan">“Pflege neu gedacht:<br>wirtschaftlich, nachhaltig,<br>zukunftssicher”</p>

  <section class="columns">
    <div class="column">
      <h2 class="column-title">Problem Pflegedienstkrise</h2>
      <p class="column-text">Fehlende Liquidität, hohe Fluktuation,<br>steigende Kosten, sinkende Auslastung</p>
    </div>
    <div class="column">
      <h2 class="column-title">Tolvek Lösung</h2>
      <p class="column-text">Analyse, klare Prozesse, stabile Finanzen<br>und motivierte Teams für Ihren Dienst</p>
    </div>
    <div class="column">
      <h2 class="column-title">Standorte Deutschland</h2>
      <p class="column-text">Rostock, Berlin und bundesweit<br>vor Ort für Ihren Pflegedienst tätig</p>
    </div>
    <div class="column">
      <h2 class="column-title">Tolvek GmbH</h2>
      <p class="column-text">info at tolvek-beispiel.de, Tel 0555 91827364,<br>Ihr Partner für Pflegeberatung</p>
    </div>
  </section>

  <div class="footer-rule"></div>
  <footer class="footer">
    <span>Nachhaltige Pflegeberatung bundesweit</span>
    <span>Tel 0555 91827364 | info at tolvek-beispiel.de</span>
  </footer>
</div>
</body>
</html>
```